VOMRA Pty Ltd Business Card

Looking for a simple yet eye-catching double-sided business card design using my company logo on one side and contact details on the other.

Target Market(s)

Government

Industry/Entity Type

Communication Systems Engineering

Contact Information for Business Card

VOMRA Pty Ltd

Requirements
Nice to have
• Would be great to have a QR code so details can be scanned into contacts

```html
<!DOCTYPE html>
<html lang="en">
<head>
<meta charset="utf-8">
<title>VOMRA Pty Ltd Business Card</title>
<link href="https://fonts.googleapis.com/css2?family=Open+Sans:wght@400;600;700&display=swap" rel="stylesheet">
<style>
  :root {
    --backdrop: #222222;
    --card: #37424a;
    --gold: #e8b52a;
    --gold-deep: #c99520;
    --icon-ink: #37424a;
  }
  * { box-sizing: border-box; margin: 0; padding: 0; }
  html, body {
    width: 1200px; height: 780px; overflow: hidden;
    background: var(--backdrop);
    font-family: "Open Sans", Arial, sans-serif;
    color: var(--gold);
  }
  .stage {
    width: 1200px; height: 780px;
    display: flex; justify-content: center; align-items: center; gap: 80px;
  }
  .card {
    width: 360px; height: 630px;
    background: var(--card);
    border-radius: 28px;
    box-shadow: 0 14px 30px rgba(0,0,0,.55);
    position: relative;
  }

  /* Logo side */
  .card-back {
    display: flex; flex-direction: column; align-items: center; justify-content: center; gap: 18px;
  }
  .brand-mark {
    width: 22px; height: 22px; border-radius: 50%; background: var(--gold);
  }
  .brand-name-large {
    font-weight: 700; font-size: 64px; letter-spacing: 6px; color: var(--gold);
  }
  .brand-emblem-area {
    width: 190px; height: 150px; border-radius: 12px;
    background: radial-gradient(circle, rgba(232,181,42,.35), rgba(201,149,32,.08));
  }

  /* Contact side */
  .card-front { padding: 44px 30px 0; }
  .brand-row { display: flex; align-items: center; gap: 12px; }
  .brand-row .brand-mark { width: 16px; height: 16px; }
  .brand-name-small { font-weight: 700; font-size: 34px; letter-spacing: 4px; color: var(--gold); }

  .person { margin-top: 230px; text-align: center; }
  .person-name { font-weight: 700; font-size: 30px; line-height: 1.1; }
  .person-role { font-weight: 600; font-size: 15px; margin-top: 2px; }

  .dot-rule {
    display: flex; align-items: center; justify-content: center; gap: 6px;
    margin: 16px 0 10px;
  }
  .dot { border-radius: 50%; background: var(--gold); flex: none; }
  .d1 { width: 4px; height: 4px; } .d2 { width: 6px; height: 6px; }
  .d3 { width: 8px; height: 8px; } .d4 { width: 10px; height: 10px; }
  .d5 { width: 12px; height: 12px; }
  .icon-badge {
    width: 24px; height: 24px; border-radius: 50%; background: var(--gold-deep);
    display: flex; align-items: center; justify-content: center; flex: none;
  }
  .icon-badge svg { width: 14px; height: 14px; fill: none; stroke: var(--icon-ink); stroke-width: 2; stroke-linecap: round; stroke-linejoin: round; }

  .contact-list { list-style: none; text-align: center; font-size: 14px; line-height: 1.55; }
  .address { text-align: center; font-size: 14px; line-height: 1.5; }
</style>
</head>
<body>
<main class="stage">
  <section class="card card-back" aria-label="Card logo side">
    <span class="brand-mark"></span>
    <div class="brand-name-large">VOMRA</div>
    <div class="brand-emblem-area" role="img" aria-label="Circuit-board tree emblem"></div>
  </section>

  <section class="card card-front" aria-label="Card contact side">
    <div class="brand-row">
      <div class="brand-emblem-area" role="img" aria-label="Circuit-board tree emblem" style="width:70px;height:60px;border-radius:8px;"></div>
      <span class="brand-mark"></span>
      <span class="brand-name-small">VOMRA</span>
    </div>

    <div class="person">
      <h1 class="person-name">Jordan Hale</h1>
      <p class="person-role">Co-Founder</p>
    </div>

    <div class="dot-rule">
      <span class="dot d1"></span><span class="dot d2"></span><span class="dot d3"></span><span class="dot d4"></span><span class="dot d5"></span>
      <span class="icon-badge"><svg viewBox="0 0 24 24"><path d="M5 3h4l2 5-3 2a11 11 0 0 0 6 6l2-3 5 2v4a2 2 0 0 1-2 2A17 17 0 0 1 3 5a2 2 0 0 1 2-2z"/></svg></span>
      <span class="icon-badge"><svg viewBox="0 0 24 24"><rect x="3" y="5" width="18" height="14" rx="2"/><path d="M3 7l9 6 9-6"/></svg></span>
      <span class="icon-badge"><svg viewBox="0 0 24 24"><circle cx="12" cy="12" r="9"/><path d="M3 12h18M12 3a14 14 0 0 1 0 18M12 3a14 14 0 0 0 0 18"/></svg></span>
      <span class="dot d5"></span><span class="dot d4"></span><span class="dot d3"></span><span class="dot d2"></span><span class="dot d1"></span>
    </div>

    <ul class="contact-list">
      <li>(555) 014-2290</li>
      <li>www.vomra.com.au</li>
      <li>admin@vomra.com.au</li>
    </ul>

    <div class="dot-rule">
      <span class="dot d1"></span><span class="dot d2"></span><span class="dot d3"></span><span class="dot d4"></span><span class="dot d5"></span>
      <span class="icon-badge"><svg viewBox="0 0 24 24"><path d="M12 21s-7-6.5-7-12a7 7 0 0 1 14 0c0 5.5-7 12-7 12z"/><circle cx="12" cy="9" r="2.5"/></svg></span>
      <span class="dot d5"></span><span class="dot d4"></span><span class="dot d3"></span><span class="dot d2"></span><span class="dot d1"></span>
    </div>

    <address class="address" style="font-style:normal;">
      42-44 Harbour Lane Eastwood<br>NSW 2122 Australia
    </address>
  </section>
</main>
</body>
</html>
```